Modern Label for cleaning products for the brand Vorlix

We need a label design for our line of cleaning products. The label should feature our logo and an image to identify the product's intended use. I've added our logo and an image for use. This only concerns the design of the label on the front of the bottle.

Label dimensions:
Label 1 (500ml bottle with spray): width 58mm x height 115mm
Label 2: (1L bottle): width 73mm x height 140mm
The design must be consistent for both bottles which you find in the pictures.

The bottles to be labeled are white. See the attachment for a photo of the bottles.

The photo must also appear on the label to identify the product's intended use.

Product information:
Brand: Vorlix
Product: Sanitary Cleaner

This text must be placed on the label:
"Cleans, descales & freshens. followed with this text: "Ideal for quick and powerful cleaning. A ready-to-use product for everyday use."

- Mention the seperate USP's: Sanitary, Bathroom, Toilet, Wet areas

Appearance: This is a consumer product, but it must have a professional appearance. We would like to see a design that use the color blue from our logo.

Target Market(s)

Consumers who take care of their homes and want to maintain it the correct (professional) way

Font styles to use
Sans Serif

Colors
0054AA
0677BA
7BADD7
CADEEF
E8F1F8

Requirements
Must have
• USP's + use of image and logo + blend in 1 design
Nice to have
• Keep the color of the logo in the design
Should not have
• Comic sans

```html
<!DOCTYPE html>
<html lang="en">
<head>
<meta charset="utf-8">
<title>Vorlix Sanitary Cleaner – Front Label</title>
<link rel="stylesheet" href="https://fonts.googleapis.com/css2?family=Barlow+Condensed:ital,wght@0,600;0,700;1,500;1,600;1,700;1,800&family=Nunito:wght@900&display=swap">
<style>
  :root {
    --deep-blue: #0054AA;
    --brand-blue: #0677BA;
    --label-blue: #1a82cf;
    --frame-blue: #3d9ce0;
    --band-blue: #0f86d6;
    --soft-blue: #7BADD7;
    --pale-blue: #CADEEF;
    --mist: #E8F1F8;
    --stone: #b9bbbc;
    --ink: #0a0a0a;
    --white: #ffffff;
  }
  * { box-sizing: border-box; margin: 0; padding: 0; }
  html, body {
    width: 1200px; height: 784px; overflow: hidden;
    background: var(--white);
  }
  .canvas { position: relative; width: 1200px; height: 784px; }

  .label {
    position: absolute; left: 424px; top: 42px;
    width: 352px; height: 700px;
    border-radius: 16px;
    background: var(--frame-blue);
    padding: 6px;
    font-family: "Barlow Condensed", sans-serif;
    color: var(--white);
    overflow: hidden;
  }
  .label-face {
    position: relative; width: 100%; height: 100%;
    border-radius: 11px; overflow: hidden;
    background:
      repeating-linear-gradient(135deg, rgba(255,255,255,0.04) 0 1px, transparent 1px 5px),
      linear-gradient(180deg, var(--label-blue) 0%, #1c86d2 55%, #2b8fd6 100%);
  }

  .tagline {
    position: absolute; top: 28px; left: 0; right: 0;
    text-align: center; font-style: italic; font-weight: 600;
    font-size: 17px; letter-spacing: 0.2px;
  }

  .brand {
    position: absolute; top: 62px; left: 0; right: 0;
    display: flex; flex-direction: column; align-items: center;
  }
  .brand-mark {
    width: 70px; height: 70px; border-radius: 50%;
    background: var(--brand-blue);
    border: 4px solid var(--white);
  }
  .brand-name {
    margin-top: 2px;
    font-family: "Nunito", sans-serif; font-weight: 900;
    font-size: 32px; line-height: 1; color: var(--ink);
    letter-spacing: -0.5px;
  }

  .product-name {
    position: absolute; top: 196px; left: 38px;
    font-style: italic; font-weight: 800;
    font-size: 84px; line-height: 0.8; letter-spacing: 0.5px;
    text-transform: uppercase;
  }
  .product-name span { display: block; }

  .claims {
    position: absolute; top: 364px; left: 0; right: 0; text-align: center;
  }
  .claims-main {
    font-weight: 700; font-size: 20px; line-height: 1;
    text-transform: uppercase;
  }
  .claims-sub {
    margin-top: 4px;
    font-style: italic; font-weight: 700; font-size: 13px;
    color: var(--ink); text-transform: uppercase; line-height: 1;
  }

  .scene-photo {
    position: absolute; left: 0; right: 0; top: 404px; bottom: 26px;
    background:
      linear-gradient(90deg, rgba(150,160,170,0.55) 0%, rgba(150,160,170,0) 30%, rgba(255,255,255,0) 70%, rgba(160,165,170,0.45) 100%),
      linear-gradient(180deg, rgba(43,143,214,1) 0%, var(--pale-blue) 22%, var(--mist) 45%, #dcdfe1 72%, var(--stone) 100%);
  }

  .net-content {
    position: absolute; left: 20px; top: 605px;
    color: var(--ink); font-weight: 600; line-height: 0.9;
    transform: scaleX(0.8); transform-origin: left top;
  }
  .net-content .net-label { font-size: 17px; }
  .net-content .net-volume { font-size: 34px; letter-spacing: -1px; }

  .uses-band {
    position: absolute; left: 88px; right: 0; top: 603px; bottom: 22px;
    background: var(--band-blue);
    clip-path: polygon(20px 0, 100% 0, 100% 100%, 0 100%);
  }
  .uses-title {
    position: absolute; left: 114px; top: 608px;
    font-style: italic; font-weight: 700; font-size: 14px;
    text-transform: uppercase;
  }
  .uses-list {
    position: absolute; left: 96px; right: 10px; top: 630px;
    display: flex; justify-content: space-around; list-style: none;
  }
  .use-item {
    display: flex; flex-direction: column; align-items: center;
    width: 60px;
  }
  .use-icon { width: 28px; height: 28px; fill: var(--ink); }
  .use-name {
    margin-top: 6px; font-style: italic; font-weight: 500;
    font-size: 12px; text-transform: uppercase; white-space: nowrap;
  }
</style>
</head>
<body>
<main class="canvas">
  <article class="label">
    <div class="label-face">
      <p class="tagline">A READY-TO-USE PRODUCT FOR EVERYDAY USE.</p>

      <div class="brand">
        <div class="brand-mark"></div>
        <p class="brand-name">vorlix</p>
      </div>

      <h1 class="product-name"><span>Sanitary</span><span>Cleaner</span></h1>

      <div class="claims">
        <p class="claims-main">-Cleans, descales &amp; freshens-</p>
        <p class="claims-sub">Ideal for quick and powerful cleaning.</p>
      </div>

      <div class="scene-photo" role="img" aria-label="Photo of a bright modern bathroom with glass shower, white washbasin cabinet, pebble-tiled bathtub and towel radiator"></div>

      <div class="net-content">
        <p class="net-label">NET WT</p>
        <p class="net-volume">500ML</p>
      </div>

      <div class="uses-band"></div>
      <p class="uses-title">Suitable for:</p>
      <ul class="uses-list">
        <li class="use-item">
          <svg class="use-icon" viewBox="0 0 24 24"><path d="M2 13l3-3 5 5L20 4l3 3-13 13z"/></svg>
          <span class="use-name">Sanitary</span>
        </li>
        <li class="use-item">
          <svg class="use-icon" viewBox="0 0 24 24">
            <path d="M18 24V8a4 4 0 0 0-8 0v1h-1.5V8a5.5 5.5 0 0 1 11 0v16z"/>
            <path d="M6 10h8l1 3H5z"/>
            <circle cx="6" cy="16" r="1"/><circle cx="9" cy="17" r="1"/><circle cx="12" cy="16" r="1"/>
            <circle cx="5" cy="19.5" r="1"/><circle cx="8.5" cy="20.5" r="1"/><circle cx="12" cy="19.5" r="1"/>
          </svg>
          <span class="use-name">Bathroom</span>
        </li>
        <li class="use-item">
          <svg class="use-icon" viewBox="0 0 24 24">
            <rect x="11" y="1" width="9" height="9" rx="1.5"/>
            <path d="M4 11h17a1 1 0 0 1 0 2c-1 4-3 5-5 5.5V22H9v-3.5C6 17.5 4 15 4 11z"/>
          </svg>
          <span class="use-name">Toilet</span>
        </li>
        <li class="use-item">
          <svg class="use-icon" viewBox="0 0 24 24">
            <path d="M15 1l2 7 6 2-6 2-2 8-2-8-6-2 6-2z"/>
            <path d="M5 12l1 3 3 1-3 1-1 3-1-3-3-1 3-1z"/>
            <path d="M6 2l.8 2.2L9 5l-2.2.8L6 8l-.8-2.2L3 5l2.2-.8z"/>
          </svg>
          <span class="use-name">Wet areas</span>
        </li>
      </ul>
    </div>
  </article>
</main>
</body>
</html>
```